Local Flower Farm Needs Business Card Design

I need business cards designed for a flower farm based in Eudora, Kansas.
Business Info:
We are a local cut flower farm located in Eudora, Kansas, founded by Corinne Haldwick. What started as a passion for agriculture and search for more joy in daily life has blossomed into a small business dedicated to providing the community with beautiful, fresh, and sustainable flowers. We specialize in local, seasonal blooms, ensuring that every petal reflects the care and dedication we pour into our craft. Our mission is to deliver the highest quality flowers directly to our customers through local farmers markets and to florists who share our commitment to sustainability. Join us in celebrating the beauty of nature, one bloom at a time!
Contact Details:
Corinne Haldwick
Owner
Phone 913-555-0147
Facebook: Rosalind Thorpe Gardens
Instagram: @RosalindThorpeGardens
Website: RosalindThorpeGardens.example
Target Market(s)
Wholesale to Florists and Direct to Consumer via Farmers Market
Industry/Entity Type
Florist, Farm
Contact Information for Business Card
Name, Contact Info, Logo
Look and feel
Each slider illustrates characteristics of the customer's brand and the style your logo design should communicate.

```html
<!DOCTYPE html>
<html lang="en">
<head>
<meta charset="utf-8">
<title>Rosalind Thorpe Gardens – Business Cards</title>
<link href="https://fonts.googleapis.com/css2?family=Tinos:wght@400;700&display=swap" rel="stylesheet">
<style>
  :root {
    --backdrop: #1b1d20;
    --paper: #ffffff;
    --ink: #0f2a30;
    --teal-deep: #0a1a20;
    --teal-mid: #0c2f38;
    --teal-light: #0e3a45;
    --cream: #ffffff;
    --rule: rgba(255,255,255,0.85);
  }
  * { box-sizing: border-box; margin: 0; padding: 0; }
  html, body {
    width: 1200px; height: 840px; overflow: hidden;
    background: var(--backdrop);
    font-family: "Tinos", "Times New Roman", serif;
  }
  .canvas {
    width: 1200px; height: 840px;
    display: flex; align-items: center; justify-content: center; gap: 40px;
  }
  .card {
    width: 560px; height: 320px; border-radius: 22px;
    position: relative; overflow: hidden;
    box-shadow: 0 18px 40px rgba(0,0,0,0.55);
  }
  .card--front { background: var(--paper); }
  .card--back {
    background: linear-gradient(135deg, var(--teal-deep) 0%, var(--teal-mid) 60%, var(--teal-light) 100%);
    color: var(--cream);
  }
  .brand-seal {
    position: absolute; border-radius: 50%;
    display: flex; align-items: center; justify-content: center; text-align: center;
    text-transform: uppercase; line-height: 1.45;
  }
  .card--front .brand-seal {
    width: 200px; height: 200px; left: 180px; top: 60px; padding: 0 28px;
    border: 1.5px solid var(--ink); color: var(--ink);
    font-size: 14px; letter-spacing: 0.1em;
  }
  .card--back .brand-seal {
    width: 156px; height: 156px; left: 362px; top: 20px; padding: 0 22px;
    border: 1.2px solid var(--cream); color: var(--cream);
    font-size: 11px; letter-spacing: 0.08em;
  }
  .divider {
    position: absolute; left: 40px; right: 22px; top: 190px;
    height: 1px; background: var(--rule);
  }
  .person { position: absolute; left: 40px; top: 132px; }
  .person__name { font-weight: 700; font-size: 25px; letter-spacing: 0.02em; text-transform: uppercase; }
  .person__role { font-size: 16px; margin-top: 1px; }
  .contact { position: absolute; list-style: none; font-size: 16px; }
  .contact li { display: flex; align-items: center; gap: 8px; margin-bottom: 6px; }
  .contact--left { left: 40px; top: 214px; }
  .contact--right { left: 318px; top: 214px; }
  .contact svg { width: 15px; height: 15px; flex: none; }
  .social-mark { width: 13px; height: 13px; border-radius: 50%; background: var(--cream); flex: none; margin: 0 1px; }
</style>
</head>
<body>
  <main class="canvas">
    <section class="card card--front" aria-label="Card front">
      <div class="brand-seal">Rosalind Thorpe<br>Gardens</div>
    </section>

    <section class="card card--back" aria-label="Card back">
      <div class="brand-seal">Rosalind Thorpe<br>Gardens</div>
      <div class="person">
        <h1 class="person__name">Corinne Haldwick</h1>
        <p class="person__role">Owner</p>
      </div>
      <div class="divider"></div>
      <ul class="contact contact--left">
        <li>
          <svg viewBox="0 0 16 16" aria-hidden="true"><path fill="#fff" d="M3.6 1.5l2.3 2.6-1.2 1.6c.9 2 2.5 3.6 4.5 4.5l1.6-1.2 2.6 2.3-1.3 2.2C7 13.4 2.6 9 2.5 4.1z"/></svg>
          913-555-0147
        </li>
        <li>
          <svg viewBox="0 0 16 16" aria-hidden="true"><circle cx="8" cy="8" r="6.5" fill="none" stroke="#fff" stroke-width="1.4"/><ellipse cx="8" cy="8" rx="2.8" ry="6.5" fill="none" stroke="#fff" stroke-width="1.2"/><line x1="1.5" y1="8" x2="14.5" y2="8" stroke="#fff" stroke-width="1.2"/></svg>
          RosalindThorpeGardens.example
        </li>
      </ul>
      <ul class="contact contact--right">
        <li><span class="social-mark"></span>Rosalind Thorpe Gardens</li>
        <li><span class="social-mark"></span>@RosalindThorpeGardens</li>
      </ul>
    </section>
  </main>
</body>
</html>
```